Business Card for Graphic Design Firm

This project is for a new graphic design firm based in New Jersey called Velmoria. We outsource graphic design and marketing jobs. We want to communicate that this is a professional company but it as well creative and artistic. This card may be used as a horizontal double sided paper card or a vertical single sided translucent card so feel free to submit designs in whichever format or both.
Updates

Reason: Extending the deadline because I'm not exactly satisfied with the designs so far.

Please view the updated project brief

Target Market(s)

Adults aged 25-60

Industry/Entity Type

Graphic Design

Font styles to use
Serif
Sans Serif

Requirements
Nice to have
• Maybe a triangular pattern around the edges similar to our logo

```html
<!DOCTYPE html>
<html lang="en">
<head>
<meta charset="utf-8">
<title>Velmoria – Business Card</title>
<link rel="stylesheet" href="https://fonts.googleapis.com/css2?family=Open+Sans:wght@400;600;700&display=swap">
<style>
  :root {
    --backdrop: #2a2a2c;
    --paper: #ffffff;
    --paper-grey: #f1f1f1;
    --ink-dark: #2b2a2b;
    --brand-teal: #1f7f9c;
    --brand-grey: #8a9599;
    --accent-orange: #f2a71b;
    --text-light: #f4f4f4;
  }
  * { margin: 0; padding: 0; box-sizing: border-box; }
  html, body {
    width: 1200px; height: 800px; overflow: hidden;
    background: var(--backdrop);
    font-family: "Open Sans", Arial, sans-serif;
  }
  .canvas { position: relative; width: 1200px; height: 800px; }

  .card {
    position: absolute; width: 520px; height: 300px;
    box-shadow: 0 10px 30px rgba(0,0,0,.45);
    overflow: hidden;
  }
  .card--front { left: 90px; top: 100px; background: var(--paper); }
  .card--back  { left: 590px; top: 400px; background: var(--paper-grey); }

  .front-name {
    position: absolute; inset: 0;
    display: flex; align-items: center; justify-content: center;
    font-size: 72px; font-weight: 600; letter-spacing: 4px;
    color: var(--brand-teal); text-transform: uppercase;
  }

  .back-panel { position: absolute; inset: 0; width: 100%; height: 100%; }

  .back-logo {
    position: absolute; left: 22px; top: 125px; width: 160px;
    text-align: center; font-size: 24px; font-weight: 600;
    letter-spacing: 2px; color: var(--brand-grey); text-transform: uppercase;
  }
  .back-wordmark {
    position: absolute; right: 24px; top: 26px;
    font-size: 34px; font-weight: 600; letter-spacing: 3px;
    color: var(--brand-teal); text-transform: uppercase;
  }

  .contact { position: absolute; left: 232px; top: 128px; color: var(--text-light); }
  .contact__name { font-size: 15px; font-weight: 700; }
  .contact__role { font-size: 11px; color: var(--accent-orange); margin-bottom: 12px; }
  .contact__row {
    display: flex; align-items: center; gap: 10px;
    font-size: 11px; margin-bottom: 10px; line-height: 1.35;
  }
  .contact__row svg { flex: none; }
</style>
</head>
<body>
<main class="canvas">

  <section class="card card--front" aria-label="Card front">
    <div class="front-name">Velmoria</div>
  </section>

  <section class="card card--back" aria-label="Card back">
    <svg class="back-panel" viewBox="0 0 520 300" preserveAspectRatio="none" aria-hidden="true">
      <polygon points="225,0 520,185 520,300 190,300" fill="var(--ink-dark)"/>
    </svg>

    <div class="back-logo">Velmoria</div>
    <div class="back-wordmark">Velmoria</div>

    <div class="contact">
      <p class="contact__name">Lorin Asberg</p>
      <p class="contact__role">Hybrid Clouds</p>

      <div class="contact__row">
        <svg width="24" height="22" viewBox="0 0 24 22" aria-hidden="true">
          <polygon points="12,1 23,21 1,21" fill="none" stroke="#ddd" stroke-width="1.2"/>
          <rect x="9" y="9" width="6" height="9" rx="1" fill="var(--accent-orange)"/>
        </svg>
        <span>+41 70 555 12 34</span>
      </div>
      <div class="contact__row">
        <svg width="24" height="22" viewBox="0 0 24 22" aria-hidden="true">
          <polygon points="12,1 23,21 1,21" fill="none" stroke="#ddd" stroke-width="1.2"/>
          <rect x="7" y="11" width="10" height="7" fill="var(--accent-orange)"/>
          <polyline points="7,11 12,15 17,11" fill="none" stroke="var(--ink-dark)" stroke-width="1"/>
        </svg>
        <span>lorin@tessaro.ch</span>
      </div>
      <div class="contact__row">
        <svg width="24" height="22" viewBox="0 0 24 22" aria-hidden="true">
          <polygon points="12,1 23,21 1,21" fill="none" stroke="#ddd" stroke-width="1.2"/>
          <polygon points="12,9 17,13 17,18 7,18 7,13" fill="var(--accent-orange)"/>
        </svg>
        <span>Lindenweg 12 8400 Kestal<br>Switzerland</span>
      </div>
    </div>
  </section>

</main>
</body>
</html>
```